Business Card Design for a Software Startup

We'd like to have a business card design. We already have a logo. Basically what we need is a clean design with name, address, cellphone and phone numbers, e-mail and web site address (front) and a space on the back with our logo with the company name on the right side and some texts on the bottom.
We are a development and consulting company in Brazil with highly qualified team of professionals in Java, iOS and Android development and consulting.

Target Market(s)

CIO, IT managers of mid to big size companies

Industry/Entity Type

Business

```html
<!DOCTYPE html>
<html lang="en">
<head>
<meta charset="utf-8">
<title>VELTRO Business Card</title>
<link href="https://fonts.googleapis.com/css2?family=Source+Sans+3:wght@400;600;700&display=swap" rel="stylesheet">
<style>
  :root {
    --page-bg: #ecebe8;
    --card-white: #ffffff;
    --navy: #1c3f73;
    --blue: #1f5fa6;
    --ink: #3a3a3a;
    --muted: #6b6b6b;
    --ray-light: #dbe8f4;
    --ray-pale: #f3f7fb;
    --back-start: #0ca3e2;
    --back-mid: #1f74c0;
    --back-end: #283a78;
  }
  * { margin: 0; padding: 0; box-sizing: border-box; }
  html, body {
    width: 1200px;
    height: 720px;
    overflow: hidden;
    background: var(--page-bg);
    font-family: "Source Sans 3", "Segoe UI", sans-serif;
  }
  .canvas {
    position: relative;
    width: 1200px;
    height: 720px;
    display: flex;
    align-items: center;
    justify-content: center;
    gap: 40px;
  }
  .card {
    position: relative;
    width: 540px;
    height: 309px;
    border-radius: 3px;
    overflow: hidden;
    box-shadow: 0 6px 18px rgba(0,0,0,0.18);
  }

  /* Front */
  .card-front { background: var(--card-white); }
  .ray-panel {
    position: absolute;
    top: 0;
    right: 60px;
    width: 150px;
    height: 100%;
    background: linear-gradient(100deg, var(--ray-light) 0%, var(--ray-pale) 60%, rgba(255,255,255,0) 100%);
  }
  .brand {
    position: absolute;
    left: 40px;
    top: 48px;
    display: flex;
    align-items: center;
    gap: 12px;
  }
  .brand-square {
    width: 44px;
    height: 44px;
    border-radius: 7px;
    background: var(--navy);
  }
  .brand-name {
    font-weight: 700;
    font-size: 54px;
    line-height: 1;
    color: var(--navy);
    letter-spacing: 1px;
  }
  .person {
    position: absolute;
    right: 48px;
    top: 112px;
    text-align: right;
  }
  .person-name {
    font-weight: 700;
    font-size: 21px;
    color: var(--blue);
    line-height: 1.1;
  }
  .person-title {
    font-size: 13px;
    color: var(--muted);
  }
  .contacts {
    position: absolute;
    left: 40px;
    top: 170px;
    list-style: none;
  }
  .contacts li {
    display: flex;
    align-items: center;
    gap: 7px;
    font-size: 15px;
    color: var(--ink);
    line-height: 22px;
  }
  .contacts svg { width: 11px; height: 11px; fill: var(--ink); }
  .address {
    position: absolute;
    left: 40px;
    top: 268px;
    font-size: 13px;
    color: var(--ink);
  }

  /* Back */
  .card-back {
    background: linear-gradient(110deg, var(--back-start) 0%, var(--back-mid) 55%, var(--back-end) 100%);
  }
  .back-brand {
    position: absolute;
    left: 0;
    right: 0;
    top: 90px;
    display: flex;
    align-items: center;
    justify-content: center;
    gap: 16px;
  }
  .back-square {
    width: 70px;
    height: 70px;
    border-radius: 12px;
    background: var(--card-white);
  }
  .back-name {
    font-weight: 700;
    font-size: 52px;
    line-height: 1;
    color: var(--card-white);
    letter-spacing: 1px;
  }
  .back-web {
    position: absolute;
    left: 0;
    right: 0;
    bottom: 44px;
    text-align: center;
    font-size: 17px;
    letter-spacing: 4px;
    color: var(--card-white);
  }
</style>
</head>
<body>
<main class="canvas">

  <section class="card card-front" aria-label="Card front">
    <div class="ray-panel" role="img" aria-label="Soft pale blue diagonal light rays decoration"></div>

    <div class="brand">
      <span class="brand-square"></span>
      <span class="brand-name">VELTRO</span>
    </div>

    <div class="person">
      <p class="person-name">Your Name</p>
      <p class="person-title">Title</p>
    </div>

    <ul class="contacts">
      <li>
        <svg viewBox="0 0 12 12" aria-hidden="true"><circle cx="6" cy="6" r="5.5" fill="none" stroke="currentColor" style="stroke:#3a3a3a" stroke-width="1"/><path d="M4 3.2l1 .1.4 1.4-.7.6c.4.9 1 1.5 1.9 1.9l.6-.7 1.4.4.1 1c-.3.5-1 .7-1.6.5C5.2 7.8 4.2 6.8 3.6 5 3.4 4.3 3.6 3.6 4 3.2z"/></svg>
        123-456-7890
      </li>
      <li>
        <svg viewBox="0 0 12 12" aria-hidden="true"><rect x="3.2" y="0.8" width="5.6" height="10.4" rx="1"/><rect x="4.2" y="2" width="3.6" height="6" fill="#fff"/></svg>
        456-085-4321
      </li>
      <li>
        <svg viewBox="0 0 12 12" aria-hidden="true"><rect x="0.8" y="2.5" width="10.4" height="7" rx="1"/><path d="M1.3 3.2L6 6.6l4.7-3.4" fill="none" stroke="#fff" stroke-width="0.9"/></svg>
        yourname@veltro.com
      </li>
      <li>
        <svg viewBox="0 0 12 12" aria-hidden="true"><circle cx="6" cy="6" r="5.5"/><path d="M0.8 6h10.4M6 0.6v10.8M6 0.6c-2.4 2.8-2.4 8 0 10.8M6 0.6c2.4 2.8 2.4 8 0 10.8" fill="none" stroke="#fff" stroke-width="0.7"/></svg>
        www.veltro.com
      </li>
    </ul>

    <p class="address">Door No. Street Name, City Name, State, Zip Code</p>
  </section>

  <section class="card card-back" aria-label="Card back">
    <div class="back-brand">
      <span class="back-square"></span>
      <span class="back-name">VELTRO</span>
    </div>
    <p class="back-web">www.veltro.com</p>
  </section>

</main>
</body>
</html>
```